business card

Business card for new business.
Red and black corporate colors.
Card can have an Indsutrial feel to it. Feel free to add Rust, Bolted steel, or graphics as you see fit. We provide highly specialized services to the below mentioned industries.
Keep information out of corners so that if I want I can choose rounded corners.
Information
- front. name - title - phone - email
- Rear
Refining - Rail - Infrastructure - Mining - Energy
Calgary - Edmonton - Fort McMurray - Revelstoke - Vancouver

```html
<!DOCTYPE html>
<html lang="en">
<head>
<meta charset="utf-8">
<title>Girdwell Business Card</title>
<link href="https://fonts.googleapis.com/css2?family=Roboto:wght@400;500&family=Roboto+Condensed:wght@700&display=swap" rel="stylesheet">
<style>
  :root {
    --backdrop: #5a4938;
    --card-dark: #232323;
    --card-deep: #1b1b1b;
    --brand-red: #e30013;
    --steel-grey: #8a8a8a;
    --paper: #f4f4f4;
    --ink-grey: #555555;
    --white: #ffffff;
  }
  * { margin: 0; padding: 0; box-sizing: border-box; }
  html, body { width: 1200px; height: 960px; overflow: hidden; }
  body {
    background: var(--backdrop);
    font-family: "Roboto", Arial, sans-serif;
    position: relative;
  }
  .card {
    position: absolute;
    width: 600px;
    height: 342px;
    box-shadow: 2px 3px 4px rgba(0,0,0,0.45);
    overflow: hidden;
  }
  .card-front { left: 314px; top: 113px; background: var(--card-dark); }
  .card-back { left: 311px; top: 472px; background: var(--paper); }

  .brand-name {
    position: absolute;
    left: 44px;
    top: 104px;
    font-family: "Roboto Condensed", "Arial Narrow", sans-serif;
    font-weight: 700;
    font-size: 50px;
    line-height: 1;
    color: var(--steel-grey);
    letter-spacing: 0.5px;
  }
  .contact-band {
    position: absolute;
    left: 0; top: 250px;
    width: 600px; height: 92px;
  }
  .contact-lines {
    position: absolute;
    left: 41px; top: 267px;
    color: var(--white);
    font-size: 15px;
    line-height: 20px;
  }
  .website {
    position: absolute;
    left: 41px; top: 320px;
    color: var(--white);
    font-size: 14px;
    letter-spacing: 6.4px;
  }
  .person {
    position: absolute;
    right: 44px; top: 272px;
    text-align: right;
  }
  .person-name {
    font-family: "Roboto Condensed", "Arial Narrow", sans-serif;
    font-weight: 700;
    font-size: 24px;
    line-height: 26px;
    color: var(--white);
  }
  .person-title {
    font-size: 15px;
    font-weight: 500;
    line-height: 18px;
    color: var(--card-deep);
  }
  .back-brand {
    position: absolute;
    left: 0; right: 0; top: 100px;
    text-align: center;
    font-family: "Roboto Condensed", "Arial Narrow", sans-serif;
    font-weight: 700;
    font-size: 64px;
    line-height: 1;
    color: var(--brand-red);
  }
  .sectors {
    position: absolute;
    left: 0; right: 0; top: 256px;
    text-align: center;
    font-size: 15px;
    line-height: 18px;
    color: var(--ink-grey);
  }
  .sep { color: var(--brand-red); font-size: 11px; }
</style>
</head>
<body>
  <section class="card card-front">
    <div class="brand-name">GIRDWELL</div>
    <svg class="contact-band" viewBox="0 0 600 92" aria-hidden="true">
      <rect width="600" height="92" fill="var(--brand-red)"/>
      <path d="M0 68 H300 C335 68 350 80 370 92 H0 Z" fill="var(--card-deep)"/>
    </svg>
    <div class="contact-lines">
      <div class="phone">604 555 0192</div>
      <div class="email">info@girdwell.com</div>
    </div>
    <div class="website">www.girdwell.com</div>
    <div class="person">
      <div class="person-name">ALAN HARKER</div>
      <div class="person-title">CEO/FOUNDER</div>
    </div>
  </section>

  <section class="card card-back">
    <div class="back-brand">GIRDWELL</div>
    <div class="sectors">
      <div>Welding <span class="sep">•</span> Piping <span class="sep">•</span> Fabrication <span class="sep">•</span> Rigging</div>
      <div>Power <span class="sep">•</span> Ashcroft <span class="sep">•</span> Dunmore <span class="sep">•</span> Port Halden</div>
      <div>Ravenhill <span class="sep">•</span> Westmoor</div>
    </div>
  </section>
</body>
</html>
```